SkyvornQ Business Cards and Stationary Design

Need a design for our business cards and stationary. I want to carry on the theme of the logo. I want the business cards to have a design on the back. I would like the business cards and the stationary to carry the same theme, design scheme, and branding

Target Market(s)

Airlines and Maintenance Facilities

Industry/Entity Type

Aviation

Contact Information for Business Card

Name
Position Title
Address: 4827 Trellis Hollow Road, Wrenhaven Bay, 00417
Office Number
Mobile Number
Email
Website

Font styles to use
Serif
Sans Serif

Colors

Designer to choose colors to be used in the design.

```html
<!DOCTYPE html>
<html lang="en">
<head>
<meta charset="utf-8">
<title>SkyvornQ Business Card</title>
<link rel="stylesheet" href="https://fonts.googleapis.com/css2?family=Michroma&family=Roboto:wght@400;500&display=swap">
<style>
  :root {
    --backdrop: #2b2c2e;
    --card: #1b1c1f;
    --card-edge: #25262a;
    --emboss: #4a4c52;
    --accent: #2a9fe0;
    --accent-deep: #1a6fb0;
    --text-light: #f2f4f7;
    --text-muted: #a7abb2;
  }
  * { margin: 0; padding: 0; box-sizing: border-box; }
  html, body { width: 800px; height: 1200px; overflow: hidden; }
  body {
    background: var(--backdrop);
    font-family: "Roboto", Arial, sans-serif;
    position: relative;
  }
  .card {
    position: absolute;
    left: 80px;
    width: 640px;
    height: 366px;
    border-radius: 24px;
    background: var(--card);
    border: 1px solid var(--card-edge);
    overflow: hidden;
  }
  .card--front { top: 150px; }
  .card--back { top: 690px; }

  .brand {
    position: absolute;
    display: flex;
    align-items: center;
    gap: 14px;
    font-family: "Michroma", Arial, sans-serif;
    letter-spacing: 4px;
    white-space: nowrap;
  }
  .brand__dot { border-radius: 50%; flex: none; }
  .card--front .brand {
    left: 50%; top: 50%;
    transform: translate(-50%, -50%);
    color: var(--emboss);
    font-size: 40px;
  }
  .card--front .brand__dot { width: 38px; height: 38px; background: var(--emboss); }

  .card--back .brand {
    left: 372px; top: 170px;
    color: var(--text-light);
    font-size: 22px;
    letter-spacing: 3px;
  }
  .card--back .brand__dot { width: 26px; height: 26px; background: var(--accent); }

  .contact {
    position: absolute;
    left: 40px; top: 92px;
  }
  .contact__name {
    color: var(--accent);
    font-size: 24px;
    font-weight: 500;
  }
  .contact__title {
    color: var(--text-muted);
    font-size: 11px;
    margin-top: 4px;
  }
  .contact__list { list-style: none; margin-top: 18px; }
  .contact__item {
    display: flex; align-items: center; gap: 9px;
    color: var(--text-light);
    font-size: 11px;
    line-height: 20px;
  }
  .contact__icon { width: 11px; height: 11px; flex: none; }
  .contact__address {
    position: absolute;
    left: 40px; top: 300px;
    color: var(--text-light);
    font-size: 11px;
  }
  .edge-stripe { position: absolute; left: 0; bottom: 0; }
</style>
</head>
<body>

<section class="card card--front" aria-label="Card front">
  <div class="brand">
    <span class="brand__dot"></span>
    <span class="brand__name">SKYVORNQ</span>
  </div>
</section>

<section class="card card--back" aria-label="Card back">
  <div class="contact">
    <p class="contact__name">Marcus Delvane</p>
    <p class="contact__title">Managing Director</p>
    <ul class="contact__list">
      <li class="contact__item">
        <svg class="contact__icon" viewBox="0 0 12 12"><path fill="#2a9fe0" d="M2.5 1l2 2.2-1 1.3a7 7 0 0 0 4 4l1.3-1 2.2 2-1 1.5C5 11 1 7 1 2z"/></svg>
        <span>000 555 0148</span>
      </li>
      <li class="contact__item">
        <svg class="contact__icon" viewBox="0 0 12 12"><rect x="3" y="0.5" width="6" height="11" rx="1.2" fill="#2a9fe0"/><rect x="4" y="2" width="4" height="7" fill="#1b1c1f"/></svg>
        <span>000 555 0193</span>
      </li>
      <li class="contact__item">
        <svg class="contact__icon" viewBox="0 0 12 12"><rect x="0.5" y="2" width="11" height="8" rx="1" fill="#2a9fe0"/><path d="M1 3l5 4 5-4" stroke="#1b1c1f" stroke-width="1.2" fill="none"/></svg>
        <span>marcus@skyvornq.com</span>
      </li>
      <li class="contact__item">
        <svg class="contact__icon" viewBox="0 0 12 12"><circle cx="6" cy="6" r="5" fill="none" stroke="#2a9fe0" stroke-width="1.4"/><path d="M1 6h10M6 1c-2.5 3-2.5 7 0 10M6 1c2.5 3 2.5 7 0 10" stroke="#2a9fe0" stroke-width="1" fill="none"/></svg>
        <span>www.skyvornq.com</span>
      </li>
    </ul>
  </div>
  <p class="contact__address">4827 Trellis Hollow Road, Wrenhaven Bay, 00417</p>

  <div class="brand">
    <span class="brand__dot"></span>
    <span class="brand__name">SKYVORNQ</span>
  </div>

  <svg class="edge-stripe" width="640" height="14" viewBox="0 0 640 14" aria-hidden="true">
    <polygon points="0,2 262,2 274,14 0,14" fill="#2a9fe0"/>
    <rect x="274" y="11" width="366" height="3" fill="#1a6fb0"/>
  </svg>
</section>

</body>
</html>
```